Detail Shop Business card design

i need a business card design for my new detailing company called 'Brisk's Polish Works'. i want an all black and white design . simple, direct and to the point. i want the designer to choose a fitting font to match the logothe front should have logo, address, phone and email and the back side should have a slogan and text indicating that we offer services on anything including cars, trucks, motorcycles and RVs. slogan will read "we take pride in your ride"
maybe also very small on the back side the IG icon with Brisks_Polish_Works

phone 208.417.6352
address 3847 E Larkin Ave
Spokane WA 99214
email: BrisksPolish@mailvexo.com

Target Market(s)

all ages , auto enthusiasts

Industry/Entity Type

Automotive

Contact Information for Business Card

the front should have logo, address, phone and email and the back side should have a slogan and text indicating that we offer services on anything including cars, trucks, motorcycles and RVs. slogan will read "we take pride in your ride"

phone 208.417.6352
address 3847 E Larkin Ave
Spokane WA 99214

Colors
000000
ffffff

Requirements
Must have
• bold font and very simple design with good spacing
Nice to have
• anything creative from the designer indicating we service any types of vehicles
Should not have
• any colors ,

```html
<!DOCTYPE html>
<html lang="en">
<head>
<meta charset="utf-8">
<title>Brisk's Polish Works – Business Card</title>
<link rel="stylesheet" href="https://fonts.googleapis.com/css2?family=Oswald:wght@500;700&family=Roboto:wght@300;400;700&display=swap">
<style>
  :root {
    --ink: #000000;
    --paper: #ffffff;
    --text-grey: #6f6f6f;
    --backdrop: #e9e9e9;
    --placeholder: #4a4a4a;
  }
  * { box-sizing: border-box; margin: 0; padding: 0; }
  html, body { width: 1200px; height: 950px; overflow: hidden; }
  body {
    background: var(--backdrop);
    display: flex;
    flex-direction: column;
    align-items: center;
    justify-content: center;
    gap: 36px;
    font-family: "Roboto", Arial, sans-serif;
  }
  .card {
    position: relative;
    width: 735px;
    height: 420px;
    background: var(--paper);
    overflow: hidden;
    box-shadow: 0 2px 8px rgba(0,0,0,0.15);
  }

  /* Front */
  .band { position: absolute; inset: 0; }
  .vehicle-art {
    position: absolute;
    left: 475px; top: 150px;
    width: 220px; height: 120px;
    border-radius: 30px 30px 10px 10px;
    background: linear-gradient(180deg, var(--placeholder), var(--ink));
  }
  .holder {
    position: absolute;
    top: 34px; left: 40px;
  }
  .holder-name {
    font-weight: 700;
    font-size: 24px;
    letter-spacing: 0.5px;
    color: var(--ink);
    text-transform: uppercase;
  }
  .holder-title {
    font-weight: 400;
    font-size: 17px;
    color: var(--text-grey);
    text-transform: uppercase;
    margin-top: 2px;
  }
  .address {
    position: absolute;
    left: 40px; bottom: 150px;
    font-weight: 300;
    font-size: 17px;
    line-height: 1.5;
    color: var(--text-grey);
  }
  .contact-list {
    position: absolute;
    left: 40px; bottom: 34px;
    list-style: none;
    font-weight: 300;
    font-size: 17px;
    line-height: 1.55;
    color: var(--text-grey);
  }
  .contact-list li { display: flex; align-items: center; gap: 10px; }
  .contact-list svg { width: 14px; height: 14px; fill: var(--ink); flex: none; }

  /* Back */
  .brand {
    position: absolute;
    left: 0; right: 0; top: 78px;
    display: flex; align-items: center; justify-content: center; gap: 18px;
  }
  .brand-dot {
    width: 64px; height: 64px; border-radius: 50%;
    background: var(--ink);
  }
  .brand-name {
    font-family: "Oswald", "Arial Narrow", sans-serif;
    font-weight: 700;
    font-size: 44px;
    color: var(--ink);
    text-transform: uppercase;
    letter-spacing: 1px;
  }
  .slogan {
    position: absolute;
    left: 0; right: 0; top: 220px;
    text-align: center;
    font-family: "Oswald", "Arial Narrow", sans-serif;
    font-weight: 700;
    font-size: 30px;
    letter-spacing: 1px;
    color: var(--ink);
    text-transform: uppercase;
  }
  .rule {
    position: absolute;
    left: 160px; right: 160px; top: 272px;
    height: 2px; background: var(--ink);
  }
  .services {
    position: absolute;
    left: 0; right: 0; top: 284px;
    text-align: center;
    font-family: "Oswald", "Arial Narrow", sans-serif;
    font-weight: 500;
    font-size: 19px;
    color: var(--ink);
  }
</style>
</head>
<body>

  <section class="card card-front">
    <svg class="band" viewBox="0 0 735 420" aria-hidden="true">
      <polygon points="735,0 735,420 520,420 735,180" fill="var(--ink)"/>
      <polygon points="440,300 735,110 735,150 470,320" fill="var(--ink)"/>
    </svg>
    <div class="vehicle-art" role="img" aria-label="Illustration of a classic hot rod car in black and white"></div>

    <div class="holder">
      <p class="holder-name">Dana Whitlow</p>
      <p class="holder-title">CEO/Founder</p>
    </div>

    <address class="address">3847 E Larkin Ave<br>Spokane WA 99214</address>

    <ul class="contact-list">
      <li><svg viewBox="0 0 16 16"><path d="M3 1l3 3-2 2c1 2 4 5 6 6l2-2 3 3-2 2C7 15 1 9 1 3z"/></svg>208.417.6352</li>
      <li><svg viewBox="0 0 16 16"><path d="M4 0h8a1 1 0 011 1v14a1 1 0 01-1 1H4a1 1 0 01-1-1V1a1 1 0 011-1zm1 2v10h6V2z"/></svg>208 552 7183</li>
      <li><svg viewBox="0 0 16 16"><path d="M0 3h16v10H0zm1 1v.5l7 4.5 7-4.5V4z"/></svg>BrisksPolish@mailvexo.com</li>
      <li><svg viewBox="0 0 16 16"><circle cx="8" cy="8" r="7.5"/><path d="M1 8h14M8 .5c-3 4-3 11 0 15M8 .5c3 4 3 11 0 15" stroke="#fff" stroke-width="1" fill="none"/></svg>www.briskspolish.com</li>
    </ul>
  </section>

  <section class="card card-back">
    <div class="brand">
      <span class="brand-dot"></span>
      <span class="brand-name">Brisk's Polish Works</span>
    </div>
    <p class="slogan">We take pride in your ride</p>
    <div class="rule"></div>
    <p class="services">services on anything including cars, trucks, motorcycles &amp; RVs</p>
  </section>

</body>
</html>
```